Local Roofing/Construction company business needs new biz card design

We need a new business card design, current cards are from the start of this operation and generic at best. We are a local Construction Company (General Contractor) with a majority of our work originating from insurance claims-exterior finish work is the main focus (Roofs-Siding-Gutters etc). Heavily involved with homeowners and the low ball offers they receive from insurance company's after a insurable event takes place. I have attached some of our original logo file(s) below.

```html
<!DOCTYPE html>
<html lang="en">
<head>
<meta charset="utf-8">
<title>Ridgeline Builders – Business Card</title>
<link rel="stylesheet" href="https://fonts.googleapis.com/css2?family=Open+Sans:wght@400;600;700;800&display=swap">
<style>
  :root {
    --stage: #333333;
    --paper: #f8f6f3;
    --ink-dark: #071f26;
    --brand-green: #4cbb6c;
    --pattern-green: #47b565;
    --white: #ffffff;
  }
  * { box-sizing: border-box; margin: 0; padding: 0; }
  html, body {
    width: 1200px; height: 780px; overflow: hidden;
    background: var(--stage);
    font-family: "Open Sans", Arial, sans-serif;
  }
  .canvas {
    width: 1200px; height: 780px;
    display: flex; align-items: center; justify-content: center; gap: 40px;
  }
  .card {
    position: relative; width: 560px; height: 320px; overflow: hidden;
    box-shadow: 0 10px 24px rgba(0,0,0,.35);
  }

  /* Back side */
  .card-back { background: var(--pattern-green); }
  .card-back .pattern-fill { position: absolute; inset: 0; background: var(--pattern-green); }
  .card-back .corner-name {
    position: absolute; right: 28px; bottom: 26px;
    display: flex; align-items: center; gap: 6px;
    color: var(--white); font-weight: 800; font-size: 12px; letter-spacing: .04em; text-transform: uppercase;
  }
  .corner-name .mark-square { width: 10px; height: 10px; background: var(--white); }

  /* Front side */
  .card-front { background: var(--paper); }
  .card-front .panel-shape { position: absolute; inset: 0; }
  .front-info { position: absolute; left: 32px; top: 30px; width: 300px; color: var(--ink-dark); }
  .company-name {
    display: flex; align-items: center; gap: 8px;
    font-weight: 800; font-size: 20px; letter-spacing: .02em; text-transform: uppercase; color: var(--ink-dark);
  }
  .company-name .mark-square { width: 16px; height: 16px; background: var(--brand-green); }
  .person { position: relative; margin-top: 34px; padding-left: 14px; }
  .person::before {
    content: ""; position: absolute; left: 0; top: 6px; width: 7px; height: 48px; background: var(--brand-green);
  }
  .person-name { font-weight: 700; font-size: 26px; line-height: 1.1; }
  .person-name .first { color: var(--brand-green); }
  .person-title { font-weight: 600; font-size: 14px; margin-top: 2px; }
  .address { margin-top: 12px; padding-left: 22px; font-size: 13px; line-height: 1.35; }
  .contacts { list-style: none; margin-top: 10px; padding-left: 14px; font-size: 13px; line-height: 1.35; }
  .contacts li { display: flex; align-items: center; gap: 8px; }
  .contacts svg { width: 12px; height: 12px; flex: none; fill: var(--brand-green); }
  .front-feature {
    position: absolute; right: 18px; top: 0; bottom: 0; width: 144px;
    display: flex; flex-direction: column; justify-content: center; align-items: center; text-align: center;
    color: var(--white); font-weight: 800; text-transform: uppercase; line-height: 1.1;
  }
  .front-feature .mark-square { width: 26px; height: 26px; background: var(--white); margin-bottom: 12px; }
  .front-feature .line-1,
  .front-feature .line-2 { font-size: 22px; letter-spacing: .02em; }
</style>
</head>
<body>
<main class="canvas">
  <section class="card card-back" aria-label="Card back">
    <div class="pattern-fill" role="img" aria-label="Repeating tiled brand pattern in tonal green"></div>
    <div class="corner-name"><span class="mark-square"></span>Ridgeline Builders</div>
  </section>

  <section class="card card-front" aria-label="Card front">
    <svg class="panel-shape" viewBox="0 0 560 320" preserveAspectRatio="none" aria-hidden="true">
      <path d="M322 0 C372 70 372 250 418 320 L452 320 C392 250 380 80 330 0 Z" fill="var(--brand-green)"/>
      <path d="M334 0 C386 80 392 250 455 320 L560 320 L560 0 Z" fill="var(--ink-dark)"/>
    </svg>

    <div class="front-info">
      <div class="company-name"><span class="mark-square"></span>Ridgeline Builders</div>
      <div class="person">
        <div class="person-name"><span class="first">Marta</span> Holloway</div>
        <div class="person-title">Co-Founder</div>
      </div>
      <p class="address">245 Oak Hollow Dr, Fairfield, MO 63010</p>
      <ul class="contacts">
        <li><svg viewBox="0 0 24 24"><path d="M6.6 10.8a15.1 15.1 0 0 0 6.6 6.6l2.2-2.2a1 1 0 0 1 1-.25 11.4 11.4 0 0 0 3.6.57 1 1 0 0 1 1 1V20a1 1 0 0 1-1 1A17 17 0 0 1 3 4a1 1 0 0 1 1-1h3.5a1 1 0 0 1 1 1c0 1.25.2 2.45.57 3.57a1 1 0 0 1-.25 1z"/></svg>555-214-0187</li>
        <li><svg viewBox="0 0 24 24"><path d="M6.6 10.8a15.1 15.1 0 0 0 6.6 6.6l2.2-2.2a1 1 0 0 1 1-.25 11.4 11.4 0 0 0 3.6.57 1 1 0 0 1 1 1V20a1 1 0 0 1-1 1A17 17 0 0 1 3 4a1 1 0 0 1 1-1h3.5a1 1 0 0 1 1 1c0 1.25.2 2.450.57 3.57a1 1 0 0 1-.25 1z"/></svg>555-214-0199 (Emergency)</li>
        <li><svg viewBox="0 0 24 24"><path d="M12 2a10 10 0 1 0 0 20 10 10 0 0 0 0-20zm6.9 6h-3a15.7 15.7 0 0 0-1.4-3.6A8 8 0 0 1 18.9 8zM12 4c.8 1.2 1.5 2.5 1.9 4h-3.8c.4-1.5 1.1-2.8 1.9-4zM4.3 14a8 8 0 0 1 0-4h3.4a16.5 16.5 0 0 0 0 4zm.8 2h3a15.7 15.7 0 0 0 1.4 3.6A8 8 0 0 1 5.1 16zm3-8h-3a8 8 0 0 1 4.4-3.6C8.9 5.5 8.4 6.7 8.1 8zM12 20c-.8-1.2-1.5-2.5-1.9-4h3.8c-.4 1.5-1.1 2.8-1.9 4zm2.3-6H9.7a14.7 14.7 0 0 1 0-4h4.6a14.7 14.7 0 0 1 0 4zm.2 5.6c.6-1.1 1.1-2.3 1.4-3.6h3a8 8 0 0 1-4.4 3.6zm1.8-5.6a16.5 16.5 0 0 0 0-4h3.4a8 8 0 0 1 0 4z"/></svg>www.ridgelinebuilders.com</li>
        <li><svg viewBox="0 0 24 24"><path d="M3 5h18a1 1 0 0 1 1 1v12a1 1 0 0 1-1 1H3a1 1 0 0 1-1-1V6a1 1 0 0 1 1-1zm9 7.6L4.5 7v1.9l7.5 5.5 7.5-5.5V7z"/></svg>hello@ridgelinebuilders.com</li>
      </ul>
    </div>

    <div class="front-feature">
      <span class="mark-square"></span>
      <span class="line-1">Ridgeline</span>
      <span class="line-2">Builders</span>
    </div>
  </section>
</main>
</body>
</html>
```